Refresh of far from plain IT company website

Our web site is starting to show it's age. You can see the existing site here: www.plumbwick.net. As a growing company we want to come across as a dynamic collection of IT experts.

We want to update the design so are open to any colour palette and look, but want to retain our current table logo. We use the logo on our business cards but with a white background - see the attached file, so you don't need to keep the brown or the green.

The design should consider the range of browsers that will be looking at the site - so please show how it will look on a wide screen laptop and a 768x1024 tablet.

We want to add some pages about our team and their skills, probably with photos of each person on the team.

This is an uncoded project - the PSD files of the design is required, not coding.
Updates

Thanks everyone for the submissions so far.  It's a holiday day in the UK today but we will get some feedback on the designs so far out to you.

Target Market(s)

Architects and other creative types looking for IT support

Industry/Entity Type

Business

Font styles to use
Serif
Sans Serif

Requirements
Must have
• Must look good on a laptop and an iPad.

```html
<!DOCTYPE html>
<html lang="en">
<head>
<meta charset="utf-8">
<title>plumbwick – far from plain IT company</title>
<link rel="stylesheet" href="https://fonts.googleapis.com/css2?family=Open+Sans:wght@400;600;700&family=Arimo:wght@400;700&display=swap">
<style>
:root{
  --magenta:#9b1455;
  --magenta-bright:#d4175f;
  --magenta-deep:#b40d50;
  --gold:#e6b512;
  --gold-deep:#c99a06;
  --ink:#222;
  --body:#444;
  --cream-top:#fcfaf2;
  --cream-bottom:#efe7d1;
  --mist-top:#f7f8f9;
  --mist-bottom:#dfe2e5;
  --footer:#141414;
}
*{box-sizing:border-box;margin:0;padding:0}
html,body{width:738px;height:1200px;overflow:hidden}
body{font-family:"Open Sans",Arial,sans-serif;color:var(--ink);background:#fff;position:relative}
.abs{position:absolute}

.site-header{left:0;top:0;width:738px;height:85px;background:linear-gradient(#fff,#f3f3f3)}
.brand{left:103px;top:30px;display:flex;align-items:center;gap:8px;font-size:26px;font-weight:600;color:var(--magenta);line-height:1}
.brand-mark{width:26px;height:22px;background:var(--gold)}
.account{left:452px;top:41px;font-size:8.5px;color:var(--magenta);display:flex;gap:5px;white-space:nowrap}
.account span.sep{color:#333}
.social-top{left:534px;top:39px;display:flex;gap:3px}
.social-top i{display:block;width:14px;height:14px;border-radius:50%;background:#1f1f1f}

.main-nav{left:0;top:85px;width:738px;height:36px;background:linear-gradient(var(--magenta-bright),var(--magenta-deep))}
.main-nav ul{list-style:none;display:flex;position:absolute;left:104px;top:0;height:36px}
.main-nav li{height:36px;line-height:36px;padding:0 12px;font-size:9.6px;color:#fff;border-right:1px solid rgba(0,0,0,.12);white-space:nowrap}
.main-nav li.active{background:var(--gold);color:#333;border:none}
.main-nav li:last-child{border:none}

.hero{left:0;top:121px;width:738px;height:349px;background:radial-gradient(ellipse at 45% 40%,#6fa0e6 0%,#3b5fb3 40%,#1b2c70 100%)}
.slider-ctrl{left:317px;top:444px;width:95px;height:15px;background:#fff;border-radius:3px;display:flex;align-items:center;padding-left:6px;gap:4px}
.slider-ctrl b{font-size:8px;color:#333;line-height:1}
.slider-ctrl .dots{display:flex;gap:4px;margin-left:8px;padding-left:6px;border-left:1px solid #ccc}
.slider-ctrl .dots i{width:5px;height:5px;border-radius:50%;background:#bbb}
.slider-ctrl .dots i.on{background:#222}

.difference{left:0;top:470px;width:738px;height:182px;background:linear-gradient(var(--cream-top),var(--cream-bottom));border:1px solid #c9c4b6}
.difference h2{position:absolute;top:17px;width:100%;text-align:center;font-weight:400;font-size:14px}
.feature{position:absolute;top:56px;width:130px;text-align:center}
.feature .ring{width:62px;height:62px;margin:0 auto;border:1.5px solid var(--magenta);border-radius:50%;background:#fff;display:flex;align-items:center;justify-content:center}
.feature p{margin-top:18px;font-size:10.6px;color:#222;white-space:nowrap}

.welcome{left:0;top:652px;width:738px;height:181px;background:linear-gradient(var(--mist-top),var(--mist-bottom));border:1px solid #c8cbcf}
.devices{left:135px;top:36px;width:170px;height:116px;background:linear-gradient(#8a8a8a,#b9b9b9);border-radius:4px}
.welcome h3{position:absolute;left:346px;top:38px;font-size:11.5px;font-weight:700;color:var(--magenta)}
.welcome p{position:absolute;left:348px;top:58px;width:262px;height:62px;overflow:hidden;font-size:7.4px;line-height:15.3px;text-align:justify;color:#222}
.btn-more{position:absolute;left:349px;top:129px;width:73px;height:18px;background:linear-gradient(#f2c72a,var(--gold-deep));border:1px solid #b88d06;color:#fff;font-family:Arimo,Arial,sans-serif;font-weight:700;font-size:9px;text-align:center;line-height:16px}

.news-title{left:103px;top:852px;font-size:10.5px;color:var(--magenta)}
.news-title b{font-weight:700}
.news-arrows{left:428px;top:852px;display:flex;gap:3px}
.news-arrows i{width:10px;height:10px;border:1px solid #888;border-radius:50%;display:block;background:#fff}
.news-card{top:874px;width:174px;height:92px;background:linear-gradient(#fff,#e4e6e8);border:1px solid #cfd2d5;font-family:Arimo,Arial,sans-serif}
.news-date{position:absolute;left:8px;top:9px;width:34px;text-align:center;color:#fff;font-size:7px;line-height:9px}
.news-date .d{background:var(--gold);display:block}
.news-date .m{background:var(--gold-deep);display:block;font-size:6px}
.news-head{position:absolute;left:45px;top:9px;width:120px;font-size:7.2px;line-height:12px;color:#222;text-align:justify}
.news-body{position:absolute;left:9px;top:41px;width:158px;font-size:6.4px;line-height:9px;color:#555}
.news-link{position:absolute;left:9px;top:78px;font-size:6.4px;font-style:italic;color:var(--magenta)}

.services-title{left:472px;top:852px;font-size:10.5px;color:var(--magenta)}
.services{left:472px;top:878px;font-family:Arimo,Arial,sans-serif;font-size:8px;color:#222}
.services ul{list-style:none;margin-top:7px}
.services li{display:flex;align-items:center;gap:5px;height:15.3px}
.services li i{width:8px;height:8px;border-radius:50%;background:var(--gold);display:block}

.partners{left:0;top:993px;width:738px;height:99px;background:linear-gradient(#fff,#e6e8ea);border-top:1px solid #e2e2e2}
.partners h4{position:absolute;top:13px;width:100%;text-align:center;font-weight:400;font-size:11px;letter-spacing:.5px}
.partner-row{position:absolute;top:52px;left:108px;width:525px;display:flex;justify-content:space-between}
.partner{display:flex;align-items:center;gap:5px;font-size:13px;font-weight:600;color:#333}
.partner i{width:12px;height:12px;display:block;background:#8a8f96}

.site-footer{left:0;top:1092px;width:738px;height:108px;background:linear-gradient(#1e1e1e,var(--footer))}
.footer-links{position:absolute;top:13px;width:100%;text-align:center;font-size:7.4px;color:#fff}
.footer-links span{margin:0 4px}
.footer-social{position:absolute;top:39px;left:291px;display:flex;gap:9px}
.footer-social i{width:26px;height:26px;border-radius:50%;display:block;background:#3a3a3a;box-shadow:0 0 0 2px #2a2a2a}
.copyright{position:absolute;top:76px;width:100%;text-align:center;font-family:Arimo,Arial,sans-serif;font-size:6.8px;color:#fff}
</style>
</head>
<body>

<header class="site-header abs">
  <div class="brand abs"><span class="brand-mark"></span>plumbwick</div>
  <div class="account abs"><span>SIGN IN</span><span class="sep">|</span><span>LOG IN</span></div>
  <div class="social-top abs" aria-label="Social links"><i></i><i></i><i></i><i></i><i></i><i></i></div>
</header>

<nav class="main-nav abs">
  <ul>
    <li class="active">HOME</li><li>ABOUT US</li><li>WHAT WE DO</li><li>NEWS BLOG</li>
    <li>ARTICLES</li><li>CLIENTS</li><li>SUPPORT</li><li>CONTACT</li>
  </ul>
</nav>

<section class="hero abs" role="img" aria-label="Banner illustration: glowing cloud linked by circuit lines to computers, laptop and phone on a blue background"></section>
<div class="slider-ctrl abs"><b>&#8249;</b><b>&#8250;</b><span class="dots"><i></i><i></i><i class="on"></i><i></i><i></i><i></i></span></div>

<section class="difference abs">
  <h2>The Plumbwick Difference</h2>
  <div class="feature" style="left:103px">
    <div class="ring"><svg width="32" height="26" viewBox="0 0 32 26" fill="none" stroke="#9b1455" stroke-width="1.6"><path d="M8 17a5 5 0 0 1 0-10 7 7 0 0 1 13-1 5 5 0 0 1 4 11z"/><path d="M16 17v5M11 23h10"/></svg></div>
    <p>CLOUD COMPUTING</p>
  </div>
  <div class="feature" style="left:236px">
    <div class="ring"><svg width="30" height="30" viewBox="0 0 30 30" fill="none" stroke="#9b1455" stroke-width="1.6"><path d="M6 4h15v10M6 4v21h9"/><path d="M10 10h8M10 14h8M10 18h4"/><circle cx="21" cy="21" r="6" fill="#9b1455"/><path d="M21 18v6M18 21h6" stroke="#fff"/></svg></div>
    <p>DISASTER RECOVERY</p>
  </div>
  <div class="feature" style="left:372px">
    <div class="ring"><svg width="32" height="28" viewBox="0 0 32 28" fill="none" stroke="#9b1455" stroke-width="1.6"><rect x="3" y="3" width="26" height="17"/><path d="M7 16l6-6 4 4 8-8"/><path d="M16 20v4M10 25h12"/></svg></div>
    <p>VIRTUALISATION</p>
  </div>
  <div class="feature" style="left:508px">
    <div class="ring"><svg width="32" height="32" viewBox="0 0 32 32" fill="#9b1455"><circle cx="12" cy="13" r="7"/><circle cx="23" cy="9" r="4"/><circle cx="14" cy="25" r="4"/><circle cx="12" cy="13" r="2.5" fill="#fff"/><circle cx="23" cy="9" r="1.5" fill="#fff"/><circle cx="14" cy="25" r="1.5" fill="#fff"/></svg></div>
    <p>CAD SERVICE</p>
  </div>
</section>

<section class="welcome abs">
  <div class="devices abs" role="img" aria-label="Illustration of a desktop monitor, laptop, tablet and phone"></div>
  <h3>WELCOME TO PLUMBWICK</h3>
  <p>Plumbwick was established with a specific aim: to consistently deliver an advanced and comprehensive IT service for ambitious growing companies across all industry sectors. Plumbwick was established with a specific aim: to consistently deliver an advanced and comprehensive</p>
  <div class="btn-more">VIEW MORE</div>
</section>

<h3 class="news-title abs" style="font-weight:400">RECENT <b>NEWS</b></h3>
<div class="news-arrows abs"><i></i><i></i></div>
<article class="news-card abs" style="left:103px">
  <div class="news-date"><span class="d">03</span><span class="m">may 2014</span></div>
  <div class="news-head">Plumbwick launch phone and tablet apps</div>
  <div class="news-body">Effective immediately "Record Rooms" management can confirm that the company name and all stock has been acquired</div>
  <div class="news-link">READ MORE...</div>
</article>
<article class="news-card abs" style="left:279px">
  <div class="news-date"><span class="d">07</span><span class="m">jan 2014</span></div>
  <div class="news-head">Plumbwick launch phone and tablet apps</div>
  <div class="news-body">Finegrain Works Ltd are carrying out extensive application trials with Micro Mist Cooling to establish the benefits</div>
  <div class="news-link">READ MORE...</div>
</article>

<h3 class="services-title abs" style="font-weight:400">PLUMBWICK SERVICES</h3>
<div class="services abs">
  <p>learn more about what we offer Services:</p>
  <ul><li><i></i>Support</li><li><i></i>Consultancy</li><li><i></i>CAD</li><li><i></i>Hosting</li><li><i></i>Development</li></ul>
</div>

<section class="partners abs">
  <h4>OUR &nbsp;PARTNERS</h4>
  <div class="partner-row">
    <span class="partner"><i></i>Boxhollow</span>
    <span class="partner"><i></i>Veranta</span>
    <span class="partner"><i style="border-radius:50%"></i>Notewell</span>
    <span class="partner">Gridsafe</span>
    <span class="partner">Keepline</span>
  </div>
</section>

<footer class="site-footer abs">
  <div class="footer-links"><span>About Us</span>|<span>Advertise With Us</span>|<span>FAQ</span>|<span>Terms and Conditions</span>|<span>Privacy Policy</span>|<span>Contact Us</span></div>
  <div class="footer-social" aria-label="Social links"><i></i><i></i><i></i><i></i><i></i></div>
  <div class="copyright">Copy Right © 2014. All rights reserved.</div>
</footer>

</body>
</html>
```